Expedition Cruise Sales Website for the Polar Regions (Antarctica & Arctic)

This will be a website for selling cruises.
This site should have a homepage, a ship page, destinations, and itineraries.
I have created a file specifying each page, and it is attached.
Pages:
1. Home
2. Cruise Lines
- 2.1 Ships
3. Destinations
- 3.1 Region - 3.2 Country - 3.3 City
4. Itineraries
- 4.1 Itinerary
5. Blog / Travel Tips 6. About Us
7. Contact
Please take a look on the attached pdf
Target Market(s)
Expedition Travelers
Coding
Coded - Design and coding required
Number of Pages Required
5+ page
Font styles to use
Look and feel
Each slider illustrates characteristics of the customer's brand and the style your logo design should communicate.

```html
<!DOCTYPE html>
<html lang="en">
<head>
<meta charset="utf-8">
<title>Icebound.co – Polar Expedition Cruises</title>
<link href="https://fonts.googleapis.com/css2?family=Poppins:wght@400;500;600;700&display=swap" rel="stylesheet">
<style>
:root{
  --blue:#2d5ea8;
  --blue-dark:#234c8c;
  --ink:#1c1c1c;
  --muted:#555b66;
  --light:#eef2fa;
  --footer:#222222;
  --white:#ffffff;
  --star:#f2a516;
}
*{box-sizing:border-box;margin:0;padding:0}
html,body{width:1200px;height:4619px;overflow:hidden}
body{font-family:'Poppins',sans-serif;color:var(--ink);background:var(--white);position:relative}
.abs{position:absolute}
.section{position:absolute;left:0;width:1200px}

/* header */
.header{top:0;height:126px;background:var(--white)}
.brand{position:absolute;display:flex;flex-direction:column;align-items:center;color:var(--blue);font-weight:600}
.brand .dot{width:40px;height:40px;border-radius:50%;background:var(--blue)}
.header .brand{left:118px;top:10px;font-size:34px;gap:2px}
.contact{position:absolute;top:14px;display:flex;align-items:center;gap:10px;font-size:13px;color:var(--ink)}
.contact .ic{width:36px;height:36px;border-radius:50%;background:var(--blue);display:flex;align-items:center;justify-content:center}
.contact b{color:var(--blue);font-weight:500}
.nav{position:absolute;top:80px;left:337px;display:flex;gap:0;font-size:12.5px;font-weight:500}
.nav a{color:var(--ink);text-decoration:none;margin-right:45px}
.nav a.active{color:var(--blue);text-decoration:underline}

/* hero */
.hero{top:126px;height:559px;background:linear-gradient(180deg,#8b7566 0%,#4b5e78 30%,#2b4566 60%,#1d3452 100%)}
.hero h1{position:absolute;top:100px;width:100%;text-align:center;color:var(--white);font-size:37px;font-weight:600;line-height:50px}
.search{position:absolute;left:126px;top:294px;width:963px;height:61px;background:var(--white);border-radius:31px;display:flex;align-items:center;padding-left:24px;font-size:15px;color:#333}
.search .field{display:flex;align-items:center;justify-content:space-between;height:40px;padding-right:18px;border-right:1px solid #ccc;margin-right:18px}
.search .btn{margin-left:auto;margin-right:8px;width:164px;height:46px;border-radius:23px;background:var(--blue);color:var(--white);font-weight:600;display:flex;align-items:center;justify-content:center;font-size:15px}
.play{position:absolute;left:1049px;top:422px;width:80px;height:80px;border-radius:50%;background:var(--blue);display:flex;align-items:center;justify-content:center}

.sec-title{position:absolute;width:100%;text-align:center;font-size:37px;font-weight:600}
.sec-dot{position:absolute;left:578px;width:44px;height:44px;border-radius:50%;background:var(--blue)}

/* offers */
.offer{position:absolute;overflow:hidden;border-radius:4px;color:var(--white)}
.offer .label{position:absolute;left:18px;bottom:28px;font-size:19px;font-weight:500}
.offer .price{position:absolute;right:24px;bottom:30px;font-size:18px}
.offer .price small{font-size:13px;font-weight:600}
.deal{border:4px solid #9db8e3;border-radius:10px}
.deal h3{position:absolute;left:28px;top:108px;font-size:20px;font-weight:500}
.deal p{position:absolute;left:28px;top:150px;width:340px;font-size:13.5px;line-height:27px}
.deal .save{position:absolute;left:24px;top:240px;font-size:16px;font-weight:500}
.deal .cta{position:absolute;left:24px;top:282px;font-size:15px;font-weight:600}

/* destinations */
.dest{top:1668px;height:625px;background:linear-gradient(180deg,#ffffff 0%,#e6ecf7 60%,#e9eef8 100%)}
.dcard{position:absolute;top:203px;height:267px;background:var(--white);border-radius:10px;overflow:hidden}
.dcard .img{height:196px}
.dcard .name{display:flex;align-items:center;justify-content:center;gap:8px;height:71px;font-size:18px;font-weight:500}
.dcard.active{top:189px;height:341px;background:var(--blue);border:5px solid #a8bfe4;color:var(--white)}
.dcard.active .img{height:188px}
.dcard.active .name{height:46px}
.dcard.active p{text-align:center;font-size:13px;line-height:28px;padding:0 16px}
.arrow{position:absolute;width:36px;height:36px;border-radius:50%;border:2px solid #333;display:flex;align-items:center;justify-content:center;background:var(--white)}

/* cruise lines */
.lines{top:2293px;height:590px;background:var(--white)}
.lines .panel{position:absolute;left:0;top:0;width:536px;height:590px;background:var(--blue)}
.lines h2{position:absolute;left:107px;top:175px;color:var(--white);font-size:36px;font-weight:600}
.lines .intro{position:absolute;left:110px;top:236px;width:250px;color:var(--white);font-size:13.5px;line-height:28px}
.vm{position:absolute;left:109px;top:350px;width:162px;height:45px;border-radius:23px;background:#1c1c1c;color:var(--white);font-size:14px;font-weight:600;display:flex;align-items:center;justify-content:center}
.lcard{position:absolute;top:84px;width:264px;height:398px;background:var(--white);box-shadow:0 4px 14px rgba(0,0,0,.12);overflow:hidden}
.lcard .img{height:242px}
.lcard .lname{margin:12px 0 0 22px;font-size:34px;font-weight:500;letter-spacing:.5px}
.lcard p{margin:6px 0 0 24px;font-size:13.5px;line-height:27px;color:#333;width:220px}
.lcard .rate{margin:8px 0 0 24px;font-size:13px;color:#333}
.rate span{color:var(--star);letter-spacing:1px}

/* testimonials */
.tcard{position:absolute;top:3143px;width:311px;height:302px;background:var(--white);box-shadow:0 4px 16px rgba(0,0,0,.1)}
.tcard p{position:absolute;left:25px;top:40px;width:270px;font-size:14px;line-height:29px;color:#333}
.tcard hr{position:absolute;left:25px;right:20px;top:183px;border:0;border-top:1px solid #ddd}
.tcard .av{position:absolute;left:14px;top:192px;width:92px;height:92px;border-radius:50%;background:linear-gradient(180deg,#c9cfd6,#8a96a3)}
.tcard .who{position:absolute;left:122px;top:212px;font-size:17px;font-weight:600;color:var(--blue)}
.tcard .role{position:absolute;left:122px;top:240px;font-size:14px;color:#333}
.tcard .st{position:absolute;left:122px;top:264px;color:var(--star);font-size:14px;letter-spacing:2px}
.tcard .g{position:absolute;right:22px;top:225px;width:30px;height:30px;border-radius:50%;border:5px solid var(--blue)}
.dots{position:absolute;top:3495px;left:535px;display:flex;gap:12px}
.dots i{display:block;width:35px;height:6px;border-radius:3px;background:#b8c3e3}
.dots i.on{background:var(--blue)}

/* newsletter */
.news{top:3581px;height:590px}
.news .photo{position:absolute;inset:0;background:linear-gradient(180deg,#5e7d9e 0%,#a8bdd2 45%,#dbe5ee 75%,#8aa3bd 100%)}
.news .box{position:absolute;left:599px;top:52px;width:528px;height:463px;background:rgba(45,94,168,.92)}
.news .box .dot{position:absolute;left:242px;top:38px;width:44px;height:44px;border-radius:50%;background:var(--white)}
.news h2{position:absolute;top:130px;width:100%;text-align:center;color:var(--white);font-size:27px;font-weight:600;line-height:43px}
.input{position:absolute;left:47px;width:438px;height:48px;border-radius:24px;background:var(--white);font-size:14px;color:#333;padding-left:20px;display:flex;align-items:center}
.signup{position:absolute;left:183px;top:366px;width:162px;height:44px;border-radius:22px;background:#1c1c1c;color:var(--white);font-size:14px;font-weight:600;display:flex;align-items:center;justify-content:center}
.chat{position:absolute;left:366px;top:365px;width:46px;height:46px;border-radius:50%;background:#2fb84a}

/* footer */
.footer{top:4171px;height:448px;background:var(--footer);color:var(--white)}
.footer .brand{left:0;width:100%;top:72px;color:var(--white);font-size:34px;gap:10px}
.footer .brand .dot{background:var(--white);width:48px;height:48px}
.socials{position:absolute;top:228px;left:497px;display:flex;gap:25px}
.socials i{display:block;width:32px;height:32px;border-radius:50%;background:var(--white)}
.flinks{position:absolute;width:100%;text-align:center;font-size:13.5px}
.flinks a{color:var(--white);text-decoration:none;margin:0 20px}
.footer hr{position:absolute;left:111px;width:980px;top:368px;border:0;border-top:1px solid #777}
.copy{position:absolute;top:394px;width:100%;text-align:center;font-size:14px}
</style>
</head>
<body>

<header class="section header">
  <div class="brand"><span class="dot"></span>Icebound.co</div>
  <div class="contact" style="left:570px"><span class="ic"><svg width="16" height="16" viewBox="0 0 24 24"><path fill="#fff" d="M6.6 10.8a15 15 0 0 0 6.6 6.6l2.2-2.2c.3-.3.7-.4 1-.2 1.1.4 2.3.6 3.6.6.6 0 1 .4 1 1V20c0 .6-.4 1-1 1A17 17 0 0 1 3 4c0-.6.4-1 1-1h3.5c.6 0 1 .4 1 1 0 1.3.2 2.5.6 3.6.1.3 0 .7-.2 1z"/></svg></span><span><b>Email Us</b> info@icebound.co</span></div>
  <div class="contact" style="left:878px"><span class="ic"><svg width="16" height="16" viewBox="0 0 24 24"><path fill="#fff" d="M6.6 10.8a15 15 0 0 0 6.6 6.6l2.2-2.2c.3-.3.7-.4 1-.2 1.1.4 2.3.6 3.6.6.6 0 1 .4 1 1V20c0 .6-.4 1-1 1A17 17 0 0 1 3 4c0-.6.4-1 1-1h3.5c.6 0 1 .4 1 1 0 1.3.2 2.5.6 3.6.1.3 0 .7-.2 1z"/></svg></span><span><b>Call Us</b> +1 800 555 0142</span></div>
  <nav class="nav">
    <a class="active" href="#">HOME</a><a href="#">CRUISE LINES</a><a href="#">DESTINATIONS</a><a href="#">ITINERARIES</a><a href="#">BLOG</a><a href="#">ABOUT US</a><a href="#">CONTACT</a>
  </nav>
</header>

<section class="section hero" role="img" aria-label="Cruise ship sailing at sunset">
  <h1>Set Sail on Your Dream Cruise –<br>Explore Unforgettable Destinations and<br>Exclusive Deals!</h1>
  <div class="search">
    <div class="field" style="width:196px">Cruise Destination <svg width="16" height="18" viewBox="0 0 24 24"><path fill="none" stroke="#555" stroke-width="2" d="M12 22s7-7 7-12a7 7 0 0 0-14 0c0 5 7 12 7 12z"/><circle cx="12" cy="10" r="2.5" fill="none" stroke="#555" stroke-width="2"/></svg></div>
    <div class="field" style="width:178px">Departure Date <svg width="16" height="16" viewBox="0 0 24 24"><rect x="3" y="5" width="18" height="16" fill="none" stroke="#555" stroke-width="2"/><path d="M3 10h18M8 3v4M16 3v4" stroke="#555" stroke-width="2"/></svg></div>
    <div class="field" style="width:184px">Departure Time <svg width="16" height="16" viewBox="0 0 24 24"><circle cx="12" cy="12" r="9" fill="none" stroke="#555" stroke-width="2"/><path d="M12 7v5l3 2" fill="none" stroke="#555" stroke-width="2"/></svg></div>
    <div class="field" style="width:176px;border:0">Cruise Line <svg width="20" height="18" viewBox="0 0 24 24"><path d="M3 17l2 4h14l2-4zM6 17V11h12v6M9 11V7h6v4M12 3v4" fill="none" stroke="#555" stroke-width="1.6"/></svg></div>
    <div class="btn">SEARCH</div>
  </div>
  <div class="play"><svg width="30" height="30" viewBox="0 0 24 24"><path d="M7 4l14 8-14 8z" fill="#fff"/></svg></div>
</section>

<section class="section" style="top:685px;height:983px">
  <span class="sec-dot" style="top:82px"></span>
  <h2 class="sec-title" style="top:142px">Featured Offers</h2>
  <div class="offer" style="left:111px;top:230px;width:476px;height:341px;background:linear-gradient(180deg,#c9b0a8 0%,#8c8595 45%,#3f5168 100%)" role="img" aria-label="Cruise ship at sunset in calm waters">
    <div class="label">Best Antarctic Cruises</div><div class="price"><small>Price:</small> $2999+</div>
  </div>
  <div class="offer" style="left:610px;top:230px;width:476px;height:341px;background:linear-gradient(180deg,#7fa3cf 0%,#b9c8d9 40%,#2f5581 100%)" role="img" aria-label="Large cruise ship on open ocean">
    <div class="label">Top Galápagos Cruises</div><div class="price"><small>Price:</small> $1799+</div>
  </div>
  <div class="offer deal" style="left:107px;top:585px;width:982px;height:348px;background:linear-gradient(90deg,#173a55 0%,#1f4b66 55%,#2a6478 100%)" role="img" aria-label="Aerial view of a cruise ship deck at sea">
    <h3>Last-Minute Deals</h3>
    <p>Don't miss out on these unbeatable last-minute offers, perfect for spontaneous travelers!</p>
    <div class="save">Up to 40% off select departures.</div>
    <div class="cta">CLICK HERE TO BOOK! &nbsp;»</div>
  </div>
</section>

<section class="section dest">
  <span class="sec-dot" style="top:30px"></span>
  <h2 class="sec-title" style="top:100px">Our Destinations</h2>
  <div class="arrow" style="left:41px;top:366px"><svg width="14" height="14" viewBox="0 0 24 24"><path d="M15 5l-7 7 7 7" fill="none" stroke="#333" stroke-width="2.5"/></svg></div>
  <div class="dcard" style="left:111px;width:230px"><div class="img" role="img" aria-label="Colourful Caribbean waterfront houses" style="background:linear-gradient(180deg,#6fa3d8,#d49a4a 60%,#7c6a4f)"></div><div class="name"><svg width="22" height="22" viewBox="0 0 24 24"><path fill="none" stroke="#333" stroke-width="1.6" d="M12 19s6-6 6-10a6 6 0 0 0-12 0c0 4 6 10 6 10z"/><circle cx="12" cy="9" r="2" fill="none" stroke="#333" stroke-width="1.6"/><path d="M5 21h14" stroke="#333" stroke-width="1.6"/></svg>Caribbean</div></div>
  <div class="dcard active" style="left:341px;width:267px"><div class="img" role="img" aria-label="Mediterranean coastal village on cliffs" style="background:linear-gradient(180deg,#6d99c9,#c7a186 55%,#3c6b8f)"></div><div class="name"><svg width="24" height="24" viewBox="0 0 24 24"><path fill="none" stroke="#fff" stroke-width="1.6" d="M12 19s6-6 6-10a6 6 0 0 0-12 0c0 4 6 10 6 10z"/><circle cx="12" cy="9" r="2" fill="none" stroke="#fff" stroke-width="1.6"/><path d="M5 21h14" stroke="#fff" stroke-width="1.6"/></svg>Mediterranean</div><p>The perfect blend of history, art, and stunning landscapes.<br>Explore destinations</p></div>
  <div class="dcard" style="left:610px;width:228px"><div class="img" role="img" aria-label="Snowy Alaskan mountains with wildlife" style="background:linear-gradient(180deg,#8fb2d6,#e3ebf2 45%,#7b7560)"></div><div class="name"><svg width="22" height="22" viewBox="0 0 24 24"><path fill="none" stroke="#333" stroke-width="1.6" d="M12 19s6-6 6-10a6 6 0 0 0-12 0c0 4 6 10 6 10z"/><circle cx="12" cy="9" r="2" fill="none" stroke="#333" stroke-width="1.6"/><path d="M5 21h14" stroke="#333" stroke-width="1.6"/></svg>Alaska</div></div>
  <div class="dcard" style="left:854px;width:231px"><div class="img" role="img" aria-label="Asian city skyline by the water" style="background:linear-gradient(180deg,#5d8fcf,#c9b9a8 60%,#2a3f5c)"></div><div class="name"><svg width="22" height="22" viewBox="0 0 24 24"><path fill="none" stroke="#333" stroke-width="1.6" d="M12 19s6-6 6-10a6 6 0 0 0-12 0c0 4 6 10 6 10z"/><circle cx="12" cy="9" r="2" fill="none" stroke="#333" stroke-width="1.6"/><path d="M5 21h14" stroke="#333" stroke-width="1.6"/></svg>Asia</div></div>
  <div class="arrow" style="left:1118px;top:366px;border-color:var(--blue)"><svg width="14" height="14" viewBox="0 0 24 24"><path d="M9 5l7 7-7 7" fill="none" stroke="#2d5ea8" stroke-width="2.5"/></svg></div>
</section>

<section class="section lines">
  <div class="panel"></div>
  <span class="abs" style="left:112px;top:112px;width:44px;height:44px;border-radius:50%;background:var(--white)"></span>
  <h2>Cruise Lines</h2>
  <p class="intro">Lorem Ipsum is simply dummy text of the printing and typesetting industry.</p>
  <div class="vm">VIEW MORE</div>
  <div class="abs" style="left:110px;top:2035px"></div>
  <svg class="abs" style="left:110px;top:2720px;position:absolute" width="0" height="0"></svg>
  <div class="abs" style="left:110px;top:421px;width:34px;height:34px;border-radius:50%;border:2px solid #fff;display:flex;align-items:center;justify-content:center"><svg width="12" height="12" viewBox="0 0 24 24"><path d="M15 5l-7 7 7 7" fill="none" stroke="#fff" stroke-width="3"/></svg></div>
  <div class="abs" style="left:158px;top:421px;width:34px;height:34px;border-radius:50%;background:#fff;display:flex;align-items:center;justify-content:center"><svg width="12" height="12" viewBox="0 0 24 24"><path d="M9 5l7 7-7 7" fill="none" stroke="#2d5ea8" stroke-width="3"/></svg></div>
  <div class="lcard" style="left:395px"><div class="img" role="img" aria-label="Cruise ship beside green cliffs" style="background:linear-gradient(180deg,#6b9cc7,#4d7a8a 50%,#1e5d96)"></div><div class="lname">Nordline</div><p>Explore innovative ships with thrilling activities for all ages.</p><div class="rate"><span>★★★★★</span> (514 Reviews)</div></div>
  <div class="lcard" style="left:676px"><div class="img" role="img" aria-label="Cruise ship before a city skyline at sunset" style="background:linear-gradient(180deg,#d99a5a,#7d8fa8 50%,#2a4f7a)"></div><div class="lname">Seavora</div><p>Explore innovative ships with thrilling activities for all ages.</p><div class="rate"><span>★★★★★</span> (500 Reviews)</div></div>
  <div class="lcard" style="left:960px"><div class="img" role="img" aria-label="White cruise ship on blue sea" style="background:linear-gradient(180deg,#8fb6e0,#d6e2ee 50%,#2c6bb0)"></div><div class="lname">Aurelis</div><p>Explore innovative ships with thrilling activities for all ages.</p><div class="rate"><span>★★★★★</span> (500 Reviews)</div></div>
</section>

<span class="sec-dot" style="top:2992px"></span>
<h2 class="sec-title" style="top:3062px">Customer Testimonials</h2>
<div class="tcard" style="left:111px"><p>Lorem Ipsum is simply dummy text of the printing and typesetting industry. Lorem Ipsum has been the industry's standard dummy text</p><hr><div class="av" role="img" aria-label="Customer portrait"></div><div class="who">David</div><div class="role">Client</div><div class="st">★★★★★</div><span class="g"></span></div>
<div class="tcard" style="left:447px"><p>Lorem Ipsum is simply dummy text of the printing and typesetting industry. Lorem Ipsum has been the industry's standard</p><hr><div class="av" role="img" aria-label="Customer portrait"></div><div class="who">Simon</div><div class="role">Client</div><div class="st">★★★★★</div><span class="g"></span></div>
<div class="tcard" style="left:780px"><p>Lorem Ipsum is simply dummy text of the printing and typesetting industry. Lorem Ipsum has been the industry's standard dummy text</p><hr><div class="av" role="img" aria-label="Customer portrait"></div><div class="who">Tom</div><div class="role">Client</div><div class="st">★★★★★</div><span class="g"></span></div>
<div class="dots"><i class="on"></i><i></i><i></i></div>

<section class="section news">
  <div class="photo" role="img" aria-label="Expedition ship moving through polar ice"></div>
  <div class="box">
    <span class="dot"></span>
    <h2>Catch the Wave of Savings – Sign<br>Up for Cruise News and Offers!</h2>
    <div class="input" style="top:222px">Name</div>
    <div class="input" style="top:285px">Email Address</div>
    <div class="signup">SIGN UP</div>
    <span class="chat"></span>
  </div>
</section>

<footer class="section footer">
  <div class="brand"><span class="dot"></span>Icebound.co</div>
  <div class="socials"><i></i><i></i><i></i><i></i></div>
  <div class="flinks" style="top:290px"><a href="#">Home</a><a href="#">Cruise Lines</a><a href="#">Destinations</a><a href="#">Itineraries</a><a href="#">Blog</a><a href="#">About Us</a><a href="#">Privacy Policy</a></div>
  <div class="flinks" style="top:324px"><a href="#">Terms Of Use</a><a href="#">FAQ</a><a href="#">Contact</a></div>
  <hr>
  <div class="copy">Copyrights@2025 . Icebound.co .All Rights Reserved</div>
</footer>

</body>
</html>
```